Business cards

I would like a black background with the design I previously chose. I need 2 sets of cards. Mine will have Marlene Ridgeway, Broker/Owner, 307-481-7263 and marlene.brightharbor@quillpost.example
The second set will read, Corey Albrecht, Realtor 307-538-2409, corey.brightharbor@quillpost.example

```html
<!DOCTYPE html>
<html lang="en">
<head>
<meta charset="utf-8">
<title>Bright Harbor Business Cards</title>
<link href="https://fonts.googleapis.com/css2?family=Roboto:wght@400;500&family=Roboto+Condensed:wght@500;700&display=swap" rel="stylesheet">
<style>
  :root {
    --backdrop: #1b1b1b;
    --card: #232323;
    --silver: #c9c9c9;
    --name-grey: #b8b8b8;
    --text: #ececec;
    --rule: #9a9a9a;
  }
  html, body {
    margin: 0;
    padding: 0;
    width: 1200px;
    height: 960px;
    overflow: hidden;
    background: var(--backdrop);
  }
  .canvas {
    position: relative;
    width: 1200px;
    height: 960px;
    font-family: "Roboto", Arial, sans-serif;
    color: var(--text);
  }
  .card {
    position: absolute;
    width: 600px;
    height: 342px;
    background: var(--card);
    box-shadow: 0 4px 10px rgba(0,0,0,0.55);
    transform: scale(0.9);
    transform-origin: top left;
  }
  .card-front-broker  { left: 40px;  top: 120px; }
  .card-front-realtor { left: 620px; top: 120px; }
  .card-back          { left: 330px; top: 484px; }

  .brand {
    position: absolute;
    display: flex;
    align-items: center;
    gap: 10px;
    font-family: "Roboto Condensed", "Arial Narrow", sans-serif;
    font-weight: 700;
    color: var(--silver);
    letter-spacing: 1px;
    white-space: nowrap;
  }
  .brand-mark {
    border-radius: 50%;
    background: var(--silver);
    flex: none;
  }
  .card-front .brand {
    right: 40px;
    top: 122px;
    font-size: 24px;
    line-height: 28px;
  }
  .card-front .brand-mark { width: 22px; height: 22px; }

  .holder-name {
    position: absolute;
    left: 42px;
    top: 183px;
    margin: 0;
    font-family: "Roboto Condensed", "Arial Narrow", sans-serif;
    font-weight: 700;
    font-size: 21px;
    line-height: 26px;
    color: var(--name-grey);
    text-transform: uppercase;
  }
  .holder-title {
    position: absolute;
    left: 43px;
    top: 209px;
    margin: 0;
    font-weight: 500;
    font-size: 15px;
    line-height: 18px;
    text-transform: uppercase;
    color: var(--text);
  }
  .divider {
    position: absolute;
    left: 44px;
    top: 237px;
    width: 516px;
    height: 1px;
    background: var(--rule);
  }
  .contact-list {
    position: absolute;
    left: 42px;
    top: 250px;
    margin: 0;
    padding: 0;
    list-style: none;
    font-size: 14.5px;
    line-height: 19.5px;
  }
  .contact-list li {
    display: flex;
    align-items: center;
    gap: 8px;
    white-space: nowrap;
  }
  .contact-list svg { width: 14px; height: 14px; flex: none; }

  .card-back .brand {
    left: 0;
    right: 0;
    top: 138px;
    justify-content: center;
    font-size: 36px;
    line-height: 40px;
  }
  .card-back .brand-mark { width: 32px; height: 32px; }
  .base-line {
    position: absolute;
    left: 119px;
    top: 233px;
    width: 365px;
    height: 2px;
    background: linear-gradient(90deg, transparent, var(--silver) 30%, var(--silver) 70%, transparent);
  }
  .site-url {
    position: absolute;
    left: 0;
    right: 0;
    top: 286px;
    margin: 0;
    text-align: center;
    font-size: 15px;
    line-height: 20px;
    letter-spacing: 4px;
    color: var(--text);
  }
</style>
</head>
<body>
<div class="canvas">

  <section class="card card-front card-front-broker">
    <div class="brand"><span class="brand-mark"></span>BRIGHT HARBOR</div>
    <h1 class="holder-name">Marlene Ridgeway</h1>
    <p class="holder-title">Broker/Owner</p>
    <div class="divider"></div>
    <ul class="contact-list">
      <li>
        <svg viewBox="0 0 14 14" aria-hidden="true"><rect x="3.5" y="0.5" width="7" height="13" rx="1.2" fill="none" stroke="#cfcfcf" stroke-width="1.3"/><rect x="5" y="2.5" width="4" height="7.5" fill="#cfcfcf"/></svg>
        <span>307-481-7263</span>
      </li>
      <li>
        <svg viewBox="0 0 14 14" aria-hidden="true"><rect x="1" y="3.5" width="12" height="8" fill="#cfcfcf"/><path d="M1 3.5 L7 8 L13 3.5" fill="none" stroke="#232323" stroke-width="1.2"/></svg>
        <span>marlene.brightharbor@quillpost.example</span>
      </li>
      <li>
        <svg viewBox="0 0 14 14" aria-hidden="true"><circle cx="7" cy="7" r="6" fill="#cfcfcf"/><path d="M4 4.5 Q6 4 6.5 6 Q5 8 6.5 10 M9 3.5 Q8.5 6 10.5 7" fill="none" stroke="#232323" stroke-width="1.2"/></svg>
        <span>www.brightharbor.example</span>
      </li>
    </ul>
  </section>

  <section class="card card-front card-front-realtor">
    <div class="brand"><span class="brand-mark"></span>BRIGHT HARBOR</div>
    <h1 class="holder-name">Corey Albrecht</h1>
    <p class="holder-title">Realtor</p>
    <div class="divider"></div>
    <ul class="contact-list">
      <li>
        <svg viewBox="0 0 14 14" aria-hidden="true"><rect x="3.5" y="0.5" width="7" height="13" rx="1.2" fill="none" stroke="#cfcfcf" stroke-width="1.3"/><rect x="5" y="2.5" width="4" height="7.5" fill="#cfcfcf"/></svg>
        <span>307-538-2409</span>
      </li>
      <li>
        <svg viewBox="0 0 14 14" aria-hidden="true"><rect x="1" y="3.5" width="12" height="8" fill="#cfcfcf"/><path d="M1 3.5 L7 8 L13 3.5" fill="none" stroke="#232323" stroke-width="1.2"/></svg>
        <span>corey.brightharbor@quillpost.example</span>
      </li>
      <li>
        <svg viewBox="0 0 14 14" aria-hidden="true"><circle cx="7" cy="7" r="6" fill="#cfcfcf"/><path d="M4 4.5 Q6 4 6.5 6 Q5 8 6.5 10 M9 3.5 Q8.5 6 10.5 7" fill="none" stroke="#232323" stroke-width="1.2"/></svg>
        <span>www.brightharbor.example</span>
      </li>
    </ul>
  </section>

  <section class="card card-back">
    <div class="brand"><span class="brand-mark"></span>BRIGHT HARBOR</div>
    <div class="base-line"></div>
    <p class="site-url">www.brightharbor.example</p>
  </section>

</div>
</body>
</html>
```